Garlic Farm for Farm Sales/Restaurant sales

Need a professional, but appealing to agriculture world. We are selling 27 kinds of Organic Garlic from a farm in Simla,CO. I have uploaded logo and business information-we are going to need a template, because I will need to use it for four separate people.
-We are trying to appeal to Farm to table restaurants
-As well as growers/farmers

Target Market(s)

Agriculture Sales/Restaurants-Organic

Industry/Entity Type

Agriculture

Contact Information for Business Card

Want it to look more unique then your average kelto stock card- I want it to look amazing

Font styles to use
Sans Serif

Colors
0455a3
ec1f27
fbed22
ffffff

Requirements
Must have
• Just be creative
Nice to have
• Colorful
Should not have
• plain

```html
<!DOCTYPE html>
<html lang="en">
<head>
<meta charset="utf-8">
<title>High Plains Garlic – Business Card</title>
<link rel="stylesheet" href="https://fonts.googleapis.com/css2?family=Open+Sans:wght@400;600;700&display=swap">
<style>
  :root {
    --page-bg: #e9e6e2;
    --navy: #1f2a4d;
    --red-deep: #8e0f18;
    --red: #c5141f;
    --red-bright: #e01b26;
    --gold: #f2b42a;
    --white: #ffffff;
    --bulb-light: #f7eef0;
    --bulb-mid: #e7cfd3;
  }
  * { box-sizing: border-box; margin: 0; padding: 0; }
  html, body {
    width: 1200px; height: 969px; overflow: hidden;
    background: var(--page-bg);
    font-family: "Open Sans", Arial, sans-serif;
  }
  .card {
    position: absolute; left: 100px; top: 200px;
    width: 1000px; height: 569px;
    border-radius: 34px; overflow: hidden;
    background: linear-gradient(100deg, var(--red-deep) 20%, var(--red) 55%, var(--red-bright) 100%);
    box-shadow: 0 18px 40px rgba(0,0,0,0.18);
  }
  .card__band {
    position: absolute; left: 0; top: 0; bottom: 0; width: 160px;
    background: var(--navy);
  }
  .card__bulb {
    position: absolute; left: 22px; top: 44px;
    width: 480px; height: 480px; border-radius: 50%;
    background: radial-gradient(circle at 45% 40%, var(--bulb-light) 0%, var(--bulb-light) 45%, var(--bulb-mid) 100%);
  }
  .brand {
    position: absolute; left: 80px; top: 140px; width: 380px;
    text-align: center; color: var(--navy);
  }
  .brand__dot {
    display: block; margin: 0 auto 22px;
    width: 100px; height: 100px; border-radius: 50%;
    background: var(--red);
  }
  .brand__name {
    font-weight: 700; font-size: 60px; line-height: 1;
    letter-spacing: -1px;
  }
  .brand__sub {
    font-weight: 700; font-size: 60px; line-height: 1.05;
    letter-spacing: -1px;
  }
  .contact {
    position: absolute; right: 62px; top: 108px;
    text-align: right; color: var(--white);
  }
  .contact__name {
    color: var(--gold); font-weight: 600; font-size: 34px; letter-spacing: 0.5px;
  }
  .contact__title { font-size: 25px; margin-top: 2px; letter-spacing: 0.5px; }
  .contact__address { font-size: 24px; line-height: 34px; margin-top: 30px; }
  .contact__lines { margin-top: 14px; list-style: none; }
  .contact__line {
    display: flex; justify-content: flex-end; align-items: center; gap: 12px;
    font-size: 24px; line-height: 39px;
  }
  .contact__line svg { width: 24px; height: 24px; }
  .socials {
    display: flex; justify-content: flex-end; gap: 8px; margin-top: 22px;
  }
  .socials__item {
    width: 38px; height: 38px; border-radius: 50%;
    border: 2px solid var(--gold);
  }
</style>
</head>
<body>
  <div class="card">
    <div class="card__band"></div>
    <div class="card__bulb" role="img" aria-label="Large soft garlic bulb illustration"></div>

    <div class="brand">
      <span class="brand__dot"></span>
      <div class="brand__name">high plains</div>
      <div class="brand__sub">garlic</div>
    </div>

    <div class="contact">
      <div class="contact__name">EVAN MARSH</div>
      <div class="contact__title">CEO/FOUNDER</div>
      <div class="contact__address">P.O. Box 48<br>Aldenvale, CO 80912</div>
      <ul class="contact__lines">
        <li class="contact__line">555-014-2290
          <svg viewBox="0 0 24 24" aria-hidden="true"><path fill="#f2b42a" d="M6.6 10.8a15.1 15.1 0 0 0 6.6 6.6l2.2-2.2c.3-.3.7-.4 1-.2 1.1.4 2.3.6 3.6.6.6 0 1 .4 1 1V20c0 .6-.4 1-1 1A17 17 0 0 1 3 4c0-.6.4-1 1-1h3.5c.6 0 1 .4 1 1 0 1.3.2 2.5.6 3.6.1.3 0 .7-.2 1z"/></svg>
        </li>
        <li class="contact__line">dana@hpgarlic.com
          <svg viewBox="0 0 24 24" aria-hidden="true"><rect x="2" y="5" width="20" height="14" rx="1.5" fill="#f2b42a"/><path d="M3 6l9 7 9-7" fill="none" stroke="#c5141f" stroke-width="1.6"/></svg>
        </li>
        <li class="contact__line">www.hpgarlic.com
          <svg viewBox="0 0 24 24" aria-hidden="true"><circle cx="12" cy="12" r="10" fill="#f2b42a"/><g fill="none" stroke="#c5141f" stroke-width="1.3"><ellipse cx="12" cy="12" rx="4.5" ry="10"/><path d="M2 12h20M4 7h16M4 17h16"/></g></svg>
        </li>
      </ul>
      <div class="socials">
        <span class="socials__item"></span>
        <span class="socials__item"></span>
        <span class="socials__item"></span>
        <span class="socials__item"></span>
      </div>
    </div>
  </div>
</body>
</html>
```